Must Be Creative: Trade Show Booth for HR Conference 10x10

Design Style: high-level professional - a bit playful with our theme (read the theme) please be very creative...not boring...eye catching design that will make folks stop and think...We are going for bold. Look at the examples uploaded to this brief. Stick with clean designs professional.

Audience: HR and Talent Leaders

Size 10x10 - (114x91 - safe area 104x81)
we are not doing a podium - do not include it in your design.

Brand: Meridian Growth Studio - do not use our logo in the design. We will decide how and where to add the logo and QR code when we are done with the design. Make sure your design can accommodate a QR Code and our logo.

Brand Colors:
Navy Blue: #003366
Represents: Trust, stability, and professionalism.
Emerald Green: #009473
Represents: Growth, renewal, and prosperity. It also conveys a sense of balance and calm.
Deep Charcoal: #333333
Represents: Sophistication and strength, providing a solid background that makes other colors stand out.
Vibrant Orange: #FF6A00
Represents: Energy, enthusiasm, and warmth. It's an engaging color that can stimulate action and interaction.

FONT: bold face but soft font
Montserrat:
Roboto:
Lato:
Open Sans:

Theme Text:
Are Your Managers Driving Talent Away?
Tagline:
We Empower Leaders to Retain Talent

What we do: (Do not use "What we do text)
(This text can be included or excluded)
Equip Leaders
Engage Teams
Retain Top Talent
Ignite Inclusive Leadership

Imagine Must be Diverse Teams: (See images we uploaded)

Collaborative Teams: An image of a diverse group of professionals engaged in a collaborative work setting. This could be a roundtable discussion or a team actively engaging in a brainstorming session. Such an image would illustrate inclusivity and the dynamic interactions your training promotes.

Empowering Leadership: Consider an image that depicts a leader in action, possibly mentoring or guiding a team member. Showing a moment of teaching or a supportive interaction can powerfully convey the concept of "empower".

Inspirational Settings: An image that includes open, inviting workspace environments that suggest transparency and openness. Spaces that encourage free exchange of ideas can metaphorically represent an inclusive and engaging leadership style.

Success and Achievement: An image that captures a moment of celebration within a team—perhaps cheering or a congratulatory setting—can effectively illustrate the outcome of effective leadership and team retention.

Please ask any questions you have about this project. I've tried to paint the picture as well as I can.

Target Market(s)

HR and Talent Managers

Industry/Entity Type

Human Resources

Font styles to use
Serif
Sans Serif
Decorative

Colors
0054AA
0677BA
7BADD7
CADEEF
E8F1F8
0094D4
00A9DD
6FCCEA
C7EBF8
E9F6FB
00AB8E
00BBA5
67D7C9
C6EFE9
E9F9F6
F0912C
F2A743
F7CA91
FBE8D2
FDF5EE
EB3D1F
EC4F4E
F09395
F8D3D4
FCEDEE

Requirements
Must have
• creative design ideas
Nice to have
• incorporating the photo into the theme
Should not have
• Do not add our logo. We did not include it in the brief - we may add the logo later

```html
<!DOCTYPE html>
<html lang="en">
<head>
<meta charset="utf-8">
<title>Meridian Growth Studio – Trade Show Booth</title>
<link rel="stylesheet" href="https://fonts.googleapis.com/css2?family=Poppins:wght@400;500;600;700;800&family=Montserrat:wght@400;500&display=swap">
<style>
  :root {
    --navy: #05336b;
    --red: #dc2530;
    --orange: #ff6a00;
    --green: #009473;
    --charcoal: #222222;
    --white: #ffffff;
    --stage: #e6e6e6;
  }
  html, body {
    margin: 0;
    padding: 0;
    width: 800px;
    height: 1200px;
    overflow: hidden;
    background: var(--stage);
  }
  .booth-canvas {
    position: relative;
    width: 800px;
    height: 1200px;
  }
  .booth-board {
    position: absolute;
    left: 20px;
    top: 220px;
    width: 760px;
    height: 760px;
    box-shadow: 0 18px 40px rgba(0,0,0,0.22);
  }
  .booth-board svg { display: block; width: 100%; height: 100%; }
  .brand-name { font-family: 'Poppins', sans-serif; font-weight: 700; fill: var(--red); }
  .headline-light { font-family: 'Montserrat', sans-serif; font-weight: 500; fill: var(--charcoal); }
  .headline-accent { font-family: 'Poppins', sans-serif; font-weight: 700; fill: var(--orange); }
  .headline-hero { font-family: 'Poppins', sans-serif; font-weight: 800; fill: var(--navy); }
  .headline-bold { font-family: 'Poppins', sans-serif; font-weight: 600; fill: var(--charcoal); }
  .site-url { font-family: 'Poppins', sans-serif; font-weight: 500; fill: var(--charcoal); }
  .site-url-accent { fill: var(--red); }
  .service-label { font-family: 'Poppins', sans-serif; font-weight: 500; fill: var(--white); }
  .service-badge { fill: var(--orange); stroke: var(--white); stroke-width: 3; }
  .service-icon { fill: none; stroke: var(--white); stroke-width: 2; stroke-linecap: round; stroke-linejoin: round; }
</style>
</head>
<body>
<main class="booth-canvas">
  <section class="booth-board">
    <svg viewBox="0 0 829 829" xmlns="http://www.w3.org/2000/svg">
      <defs>
        <linearGradient id="panel-light" x1="0" y1="0" x2="1" y2="1">
          <stop offset="0" stop-color="#ffffff"/>
          <stop offset="1" stop-color="#e4e6ea"/>
        </linearGradient>
        <linearGradient id="team-photo" x1="0" y1="0" x2="1" y2="0">
          <stop offset="0" stop-color="#d9d9dc"/>
          <stop offset="0.5" stop-color="#8b929c"/>
          <stop offset="1" stop-color="#2f3440"/>
        </linearGradient>
      </defs>

      <rect class="panel-light" width="829" height="829" fill="url(#panel-light)"/>

      <path class="panel-navy" d="M315 0 H829 V829 H520 C600 700 610 560 590 460 C565 320 470 120 315 0 Z" fill="var(--navy)"/>
      <path class="panel-divider" d="M338 0 C490 120 585 320 606 460 C622 560 610 690 548 829" fill="none" stroke="var(--red)" stroke-width="3"/>

      <!-- red accent band above services -->
      <rect class="services-band" x="438" y="63" width="338" height="48" rx="24" fill="var(--red)"/>

      <g class="service-item">
        <circle class="service-badge" cx="525" cy="179" r="31"/>
        <path class="service-icon" d="M525 164 a5 5 0 1 0 0.1 0 M515 194 v-12 a10 10 0 0 1 20 0 v12 M513 176 l-6 -6 M537 176 l6 -6"/>
        <text class="service-label" x="585" y="172" font-size="23">Equip</text>
        <text class="service-label" x="585" y="200" font-size="23">Leaders</text>
      </g>
      <g class="service-item">
        <circle class="service-badge" cx="563" cy="264" r="31"/>
        <path class="service-icon" d="M555 253 a4 4 0 1 0 0.1 0 M571 253 a4 4 0 1 0 0.1 0 M547 269 a8 7 0 0 1 16 0 M563 269 a8 7 0 0 1 16 0 M549 277 l8 6 l6 -4 l6 4 l8 -6"/>
        <text class="service-label" x="613" y="258" font-size="23">Engage</text>
        <text class="service-label" x="613" y="286" font-size="23">Teams</text>
      </g>
      <g class="service-item">
        <circle class="service-badge" cx="585" cy="359" r="31"/>
        <path class="service-icon" d="M582 341 a10 10 0 1 0 0.1 0 M589 358 l9 9 M596 343 l2 4 l4 1 l-3 3 l1 4 l-4 -2 l-4 2 l1 -4 l-3 -3 l4 -1 Z M570 375 h18"/>
        <text class="service-label" x="633" y="352" font-size="23">Retain Top</text>
        <text class="service-label" x="633" y="380" font-size="23">Talent</text>
      </g>
      <g class="service-item">
        <circle class="service-badge" cx="581" cy="451" r="31"/>
        <path class="service-icon" d="M573 440 a4 4 0 1 0 0.1 0 M573 448 v12 l-6 8 M573 454 l10 -6 M585 446 l10 -10 M591 434 l4 2 M569 468 h16 v-6 h-8"/>
        <text class="service-label" x="633" y="437" font-size="23">Ignite</text>
        <text class="service-label" x="633" y="466" font-size="23">Inclusive</text>
        <text class="service-label" x="633" y="495" font-size="23">Leadership</text>
      </g>

      <text class="brand-name" x="62" y="104" font-size="30">Meridian Growth</text>
      <text class="brand-name" x="62" y="141" font-size="30">Studio</text>

      <text class="headline-light" x="56" y="229" font-size="46" textLength="235" lengthAdjust="spacingAndGlyphs">ARE YOUR</text>
      <text class="headline-accent" x="56" y="267" font-size="36" textLength="387" lengthAdjust="spacingAndGlyphs">MANAGERS DRIVING</text>
      <text class="headline-accent" x="56" y="309" font-size="47" textLength="383" lengthAdjust="spacingAndGlyphs">TALENT AWAY?</text>
      <g class="headline-rule" fill="var(--green)">
        <rect x="57" y="331" width="7" height="6"/><rect x="67" y="331" width="7" height="6"/>
        <rect x="77" y="331" width="7" height="6"/><rect x="87" y="331" width="7" height="6"/>
        <rect x="97" y="331" width="7" height="6"/><rect x="107" y="331" width="7" height="6"/>
      </g>
      <text class="headline-light" x="56" y="397" font-size="46" textLength="332" lengthAdjust="spacingAndGlyphs">WE EMPOWER</text>
      <text class="headline-hero" x="54" y="474" font-size="97" textLength="442" lengthAdjust="spacingAndGlyphs">LEADERS</text>
      <text class="headline-bold" x="56" y="526" font-size="46" textLength="437" lengthAdjust="spacingAndGlyphs">TO RETAIN TALENT</text>
      <text class="site-url" x="56" y="582" font-size="21" textLength="382" lengthAdjust="spacingAndGlyphs">www.<tspan class="site-url-accent">meridiangrowthstudio</tspan>.com</text>

      <path class="team-photo" role="img" aria-label="Photo of a diverse team of professionals standing with arms crossed, a smiling bearded leader in front on the right"
        d="M35 829 V720 C120 640 260 600 400 590 L520 575 C600 540 640 510 680 505 C740 500 780 560 800 620 L829 640 V829 Z"
        fill="url(#team-photo)"/>
    </svg>
  </section>
</main>
</body>
</html>
```